Cover for Lindqvist Review 2023 using photo provided

I need a cover (front and back) designed for the 2023 version of the Lindqvist Review, using the photo attached (may2019_) of an Inuit hunter.

I want the photo to be prominent and close to the original look (ie not too much change to the the photo, except maybe tone or shading to make it look more like a book cover).

The title should be prominent: Coastal Weavers: Trade, Craft, Memory and Exchange Across Shores.
The authors should be listed: Tapio Korhola, Marcus Dell & Celeste Varga-Moine, eds.
The Lindqvist Review 2023 logo should be on the front, and the LR2023 logo should be on the spine. The Lindqvist Review and Caldera Gateway logos should be on the back cover, which can otherwise be simple.
Back cover should also include: ISSN 4751-3096

I have included the photo for this year's cover (Inuit hunter), logos, as well as the last two covers for reference.

• A4 front and back cover with 26 mm spine

```html
<!DOCTYPE html>
<html lang="en">
<head>
<meta charset="utf-8">
<title>Lindqvist Review 2023 – Cover</title>
<link rel="stylesheet" href="https://fonts.googleapis.com/css2?family=Poppins:wght@300;400;600;700&display=swap">
<style>
  :root {
    --page-bg: #e2e2e2;
    --ink-blue: #3a4f8f;
    --ink-mauve: #7a5468;
    --ink-dark: #1f2024;
    --sky-top: #9fb4d6;
    --sky-mid: #cfdbed;
    --ice: #eef1f5;
    --ridge-dark: #5e5a5e;
    --ridge-light: #8c8790;
    --band: #3a4f8f;
    --stripe: #8fa2cc;
    --fur: #ece4cf;
    --coat: #24262c;
    --seal: #6a6660;
  }
  * { margin: 0; padding: 0; box-sizing: border-box; }
  html, body { width: 800px; height: 1200px; overflow: hidden; }
  body {
    position: relative;
    background: var(--page-bg);
    font-family: "Poppins", sans-serif;
    color: var(--ink-dark);
  }

  /* ---------- photo scene layers ---------- */
  .scene-sky {
    position: absolute; inset: 0;
    background: linear-gradient(180deg, var(--sky-top) 0%, var(--sky-mid) 45%, #e4eaf3 58%, var(--ice) 100%);
  }
  .scene-ridge {
    position: absolute;
    background: linear-gradient(180deg, var(--ridge-light) 0%, var(--ridge-dark) 100%);
    border-radius: 6px 40px 0 0;
  }
  .scene-hunter {
    position: absolute;
    background: linear-gradient(180deg, var(--coat) 0%, var(--coat) 44%, var(--fur) 58%, var(--fur) 86%, #3b3b40 100%);
    border-radius: 40px 40px 8px 8px;
  }
  .scene-seal {
    position: absolute;
    background: linear-gradient(180deg, #8a857d 0%, var(--seal) 100%);
    border-radius: 50%;
  }

  /* ---------- front cover ---------- */
  .front-cover {
    position: absolute;
    width: 308px; height: 436px;
    overflow: hidden;
  }
  .front-cover.standalone {
    left: 254px; top: 77px;
    box-shadow: 0 6px 18px rgba(0,0,0,.18);
  }
  .accent-band {
    position: absolute; left: 260px; top: 0; width: 20px; height: 100%;
    background: linear-gradient(180deg, var(--band) 0%, var(--band) 72%, rgba(58,79,143,0) 100%);
  }
  .accent-stripes {
    position: absolute; left: 260px; top: 33px; width: 20px; height: 44px;
  }
  .series-mark {
    position: absolute; left: 19px; top: 34px;
    font-size: 27px; font-weight: 700; line-height: 1.05;
    color: var(--ink-blue); text-transform: uppercase; letter-spacing: -0.5px;
  }
  .title {
    position: absolute; left: 19px; top: 106px;
    text-transform: uppercase; font-weight: 700;
  }
  .title-main  { display: block; font-size: 35px; line-height: 36px; font-weight: 700; color: var(--ink-blue); letter-spacing: -0.5px; }
  .title-accent{ display: block; font-size: 26px; line-height: 27px; font-weight: 700; color: var(--ink-mauve); }
  .title-light { display: block; font-size: 21px; line-height: 26px; font-weight: 300; color: var(--ink-dark); }
  .title-rule {
    position: absolute; left: 19px; top: 198px; width: 24px; height: 2px; background: var(--ink-blue);
  }
  .subtitle {
    position: absolute; left: 19px; top: 204px;
    font-size: 10.5px; font-weight: 600; line-height: 1.45; color: var(--ink-dark);
  }
  .editors {
    position: absolute; left: 19px; bottom: 25px;
    font-size: 10px; font-weight: 600; line-height: 1.45; color: var(--ink-dark);
  }

  /* ---------- wraparound spread ---------- */
  .spread {
    position: absolute; left: 60px; top: 673px; width: 684px; height: 444px;
    overflow: hidden;
    box-shadow: 0 6px 18px rgba(0,0,0,.18);
  }
  .spread .front-cover { left: 378px; top: 0; width: 306px; height: 444px; }
  .back-cover { position: absolute; left: 0; top: 0; width: 313px; height: 100%; }
  .back-series-mark {
    position: absolute; left: 30px; top: 36px;
    font-size: 14px; font-weight: 700; line-height: 1.05;
    color: var(--ink-blue); text-transform: uppercase;
  }
  .partner-mark {
    position: absolute; left: 93px; top: 350px;
    display: flex; align-items: center; gap: 7px;
    font-size: 12px; font-weight: 400; color: var(--ink-blue);
  }
  .partner-mark .dot { width: 9px; height: 9px; border-radius: 50%; background: var(--ink-blue); }
  .issn {
    position: absolute; left: 87px; top: 390px;
    font-size: 19px; font-weight: 300; color: var(--ink-dark);
  }
  .issn strong { font-weight: 700; }
  .spine { position: absolute; left: 313px; top: 0; width: 65px; height: 100%; }
  .spine-mark {
    position: absolute; left: 50%; top: 36px; transform: translateX(-50%);
    writing-mode: vertical-rl;
    font-size: 15px; font-weight: 700; color: var(--ink-blue); letter-spacing: 0.5px;
  }
</style>
</head>
<body>

  <!-- front cover presented alone -->
  <section class="front-cover standalone">
    <div class="scene-sky" role="img" aria-label="Photograph of pale sky over flat sea ice"></div>
    <div class="scene-ridge" style="left:0; top:232px; width:122px; height:38px;" role="img" aria-label="Rocky ridge on the horizon"></div>
    <div class="scene-seal" style="left:-6px; top:336px; width:165px; height:34px;" role="img" aria-label="Seal lying on the ice"></div>
    <div class="accent-band"></div>
    <svg class="accent-stripes" viewBox="0 0 20 44" preserveAspectRatio="none" aria-hidden="true">
      <polygon points="0,14 20,2 20,8 0,20" fill="var(--stripe)"/>
      <polygon points="0,26 20,14 20,20 0,32" fill="var(--stripe)"/>
    </svg>
    <div class="scene-hunter" style="left:188px; top:134px; width:82px; height:254px;" role="img" aria-label="Hunter in dark jacket and fur trousers holding a rifle"></div>
    <div class="series-mark">Lindqvist<br>Review 2023</div>
    <h1 class="title">
      <span class="title-main">Coastal</span>
      <span class="title-accent">Weavers</span>
      <span class="title-light">Across Shores</span>
    </h1>
    <div class="title-rule"></div>
    <p class="subtitle">Trade | Craft | Memory<br>and Exchange.</p>
    <p class="editors">Tapio Korhola, Marcus Dell &amp;<br>Celeste Varga-Moine, eds.</p>
  </section>

  <!-- back, spine and front as one wrap -->
  <section class="spread">
    <div class="scene-sky" role="img" aria-label="Wraparound photograph of sea ice under a pale sky"></div>
    <div class="scene-ridge" style="left:0; top:230px; width:494px; height:46px;" role="img" aria-label="Long rocky ridge along the horizon"></div>
    <div class="scene-seal" style="left:353px; top:342px; width:182px; height:36px;" role="img" aria-label="Seal lying on the ice"></div>

    <div class="back-cover">
      <div class="back-series-mark">Lindqvist<br>Review 2023</div>
      <div class="partner-mark"><span class="dot"></span>Caldera Gateway</div>
      <p class="issn">ISSN <strong>4751-3096</strong></p>
    </div>

    <div class="spine">
      <div class="spine-mark">LR2023</div>
    </div>

    <div class="front-cover">
      <div class="accent-band"></div>
      <svg class="accent-stripes" viewBox="0 0 20 44" preserveAspectRatio="none" aria-hidden="true">
        <polygon points="0,14 20,2 20,8 0,20" fill="var(--stripe)"/>
        <polygon points="0,26 20,14 20,20 0,32" fill="var(--stripe)"/>
      </svg>
      <div class="scene-hunter" style="left:188px; top:138px; width:82px; height:256px;" role="img" aria-label="Hunter in dark jacket and fur trousers holding a rifle"></div>
      <div class="series-mark">Lindqvist<br>Review 2023</div>
      <h2 class="title">
        <span class="title-main">Coastal</span>
        <span class="title-accent">Weavers</span>
        <span class="title-light">Across Shores</span>
      </h2>
      <div class="title-rule"></div>
      <p class="subtitle">Trade | Craft | Memory<br>and Exchange.</p>
      <p class="editors">Tapio Korhola, Marcus Dell &amp;<br>Celeste Varga-Moine, eds.</p>
    </div>
  </section>

</body>
</html>
```